Professional Package for CPA Firm

We would like a stationery design for our new CPA Firm based in Atlanta, GA called 'Vale 8'. We work with investors to help grow investments, tax free. We would like the design to have a professional/minimal look with a 'wow' factor. We need 9.5″ x 4.125″, 9x12, and 10x13 mailing envelopes, business cards, and a letterhead. We have a logo that is already complete. For the letterhead, we would like to have space to put credentials at the bottom of the page

Industry/Entity Type

CPA, Accounting

```html
<!DOCTYPE html>
<html lang="en">
<head>
<meta charset="utf-8">
<title>Vale 8 — Stationery Package</title>
<link rel="stylesheet" href="https://fonts.googleapis.com/css2?family=Roboto:wght@300;400;500;700&display=swap">
<style>
  :root{
    --backdrop:#959595;
    --paper:#ffffff;
    --navy:#0b2a42;
    --teal:#1ea3b4;
    --coral:#f0454f;
    --ink:#4f5256;
    --ink-soft:#6b6e72;
    --label:#111111;
    --sign:#dfe8f3;
  }
  *{box-sizing:border-box;margin:0;padding:0}
  html,body{width:1200px;height:680px;overflow:hidden}
  body{background:var(--backdrop);font-family:'Roboto',sans-serif;color:var(--ink);position:relative}
  .sheet{position:absolute;background:var(--paper);overflow:hidden;box-shadow:0 1px 3px rgba(0,0,0,.12)}
  .label{position:absolute;font-weight:500;font-size:11.5px;color:var(--label);transform:translateX(-50%);white-space:nowrap}

  /* brand lockup */
  .brand{position:absolute;display:flex;flex-direction:column;align-items:center;color:var(--navy)}
  .brand-row{display:flex;align-items:center;gap:.25em}
  .brand-name{font-weight:700;letter-spacing:.06em;line-height:1;color:var(--navy)}
  .brand-dot{width:.42em;height:.42em;border-radius:50%;background:var(--coral)}
  .brand-tag{font-weight:400;letter-spacing:.12em;line-height:1;margin-top:.35em;color:var(--navy)}

  .icon{width:1em;height:1em;fill:var(--teal);flex:none}
  .contact-line{display:flex;align-items:center;gap:.45em;white-space:nowrap}

  /* letterhead */
  .letterhead{left:48px;top:32px;width:410px;height:580px}
  .letterhead .brand{left:0;right:0;top:88px}
  .letterhead .brand-name{font-size:25px}
  .letterhead .brand-tag{font-size:6.2px}
  .salutation{position:absolute;left:37px;top:163px;font-size:10px;font-weight:300;color:var(--ink)}
  .letter-body{position:absolute;left:37px;top:194px;width:342px;font-size:5.5px;line-height:8.8px;font-weight:300;color:var(--ink)}
  .letter-body p{margin-bottom:5px}
  .closing{position:absolute;left:37px;top:380px;font-size:5.8px;font-weight:300}
  .signature{position:absolute;left:34px;top:402px;width:72px;height:30px;background:var(--sign);border-radius:3px}
  .letter-corner{position:absolute;left:0;top:0;width:410px;height:580px}
  .letter-contact{position:absolute;right:26px;top:503px;font-size:7.8px;color:#fff;line-height:10.3px;text-align:right}
  .letter-contact .contact-line{justify-content:flex-end;flex-direction:row-reverse;gap:5px}
  .letter-contact .icon{font-size:7px}

  /* envelope */
  .envelope-back{left:490px;top:48px;width:354px;height:160px;background:transparent;box-shadow:none;overflow:visible}
  .envelope-back .body{position:absolute;left:0;top:0;width:354px;height:160px;background:var(--paper)}
  .envelope-back .flap{position:absolute;left:0;top:0;width:354px;height:60px}
  .envelope-back .brand{left:0;right:0;top:27px}
  .envelope-back .brand-name{font-size:10px;color:#fff}
  .envelope-front{left:544px;top:132px;width:355px;height:161px}
  .envelope-front .brand{left:20px;top:44px;align-items:flex-start}
  .envelope-front .brand-name{font-size:13px}
  .envelope-front .brand-tag{font-size:3.8px}
  .return-address{position:absolute;left:19px;top:68px;font-size:8.2px;line-height:10.4px;font-weight:400;color:var(--ink)}

  /* business cards */
  .card-front{left:934px;top:32px;width:187px;height:107px}
  .card-front .brand{left:18px;top:44px;align-items:flex-start}
  .card-front .brand-name{font-size:12px}
  .card-front .brand-tag{font-size:3.6px}
  .card-corner{position:absolute;left:0;top:0;width:187px;height:107px}
  .card-details{position:absolute;right:14px;top:52px;text-align:right;color:#fff;font-size:3.9px;line-height:5.2px}
  .card-name{color:var(--teal);font-size:5.8px;line-height:6.5px;font-weight:500;letter-spacing:.02em}
  .card-title{color:var(--teal);font-size:3.8px;margin-bottom:3px}
  .card-details .contact-line{justify-content:flex-end;flex-direction:row-reverse;gap:2px}
  .card-details .icon{font-size:3.6px}
  .card-back{left:930px;top:177px;width:193px;height:110px;background:linear-gradient(135deg,#0c3650 0%,#072338 100%)}

  /* email signatures */
  .email-one{left:496px;top:335px;width:176px;height:266px}
  .email-one .brand{left:23px;top:55px;align-items:flex-start}
  .email-one .brand-name{font-size:21px}
  .email-one .brand-tag{font-size:5.8px}
  .person-name{position:absolute;left:23px;top:101px;font-size:16.5px;font-weight:500;color:var(--teal)}
  .person-title{position:absolute;left:23px;top:126px;font-size:11px;font-weight:400;color:var(--navy)}
  .email-one .address{position:absolute;left:23px;top:149px;font-size:11px;line-height:14.2px;font-weight:300;color:var(--ink)}
  .email-one .contacts{position:absolute;left:23px;top:187px;font-size:11px;line-height:14.3px;font-weight:300;color:var(--ink)}
  .email-one .icon{font-size:8px}

  .email-two{left:699px;top:335px;width:455px;height:141px}
  .email-two .brand{left:90px;width:108px;top:56px}
  .email-two .brand-name{font-size:20px}
  .email-two .brand-tag{font-size:5.6px}
  .divider{position:absolute;width:1px;background:#3a3d42}
  .email-two .divider{left:206px;top:35px;height:71px}
  .email-two .details{position:absolute;left:229px;top:36px;font-size:11px;line-height:14.4px;font-weight:300;color:var(--ink)}
  .email-two .icon{font-size:8px}
  .email-two .contact-line{gap:9px}

  .email-three{left:695px;top:513px;width:455px;height:87px}
  .email-three .brand{left:36px;width:72px;top:35px}
  .email-three .brand-name{font-size:14px}
  .email-three .brand-tag{font-size:3.9px}
  .email-three .divider-a{left:128px;top:19px;height:50px}
  .email-three .divider-b{left:286px;top:19px;height:50px}
  .email-three .address{position:absolute;left:155px;top:23px;font-size:11px;line-height:14.2px;font-weight:300;color:var(--ink)}
  .email-three .contacts{position:absolute;left:312px;top:23px;font-size:11px;line-height:14.2px;font-weight:300;color:var(--ink)}
  .email-three .icon{font-size:8px}
  .email-three .contact-line{gap:8px}
</style>
</head>
<body>

<svg width="0" height="0" style="position:absolute" aria-hidden="true">
  <symbol id="i-phone" viewBox="0 0 16 16"><path d="M3.6 1.2l2.3 2.6-1.3 2c.9 2 2.4 3.6 4.5 4.6l2-1.3 2.7 2.3-1.4 2.6C7 13.7 2.3 9 1 3z"/></symbol>
  <symbol id="i-mobile" viewBox="0 0 16 16"><path d="M4 1h8v14H4zM5.5 2.5v9h5v-9zM7 12.5h2v1.2H7z" fill-rule="evenodd"/></symbol>
  <symbol id="i-mail" viewBox="0 0 16 16"><path d="M1 3.5h14v9H1zM2.2 4.5L8 9l5.8-4.5z" fill-rule="evenodd"/></symbol>
  <symbol id="i-web" viewBox="0 0 16 16"><path d="M8 1a7 7 0 110 14A7 7 0 018 1zm-2 3.2c-1.8.7-2.3 2.4-1.6 3.6.8 1.2 2.4.6 2.8 2 .3 1 -.3 2 .4 2.8 2-.2 2.4-2 1.8-3.1-.6-1-2-.8-2.3-2-.2-.9.9-1.6-1.1-3.3zm4.4-.6c-.6.8-.2 1.8.9 2 1 .2 1.6 1.3 1.6 2.2.6-1.6 0-3.3-2.5-4.2z" fill-rule="evenodd"/></symbol>
</svg>

<!-- Letterhead -->
<section class="sheet letterhead" aria-label="Letterhead">
  <div class="brand">
    <div class="brand-row"><span class="brand-name">VALE 8</span><span class="brand-dot"></span></div>
    <span class="brand-tag">CPAs and Tax Advisors</span>
  </div>
  <p class="salutation">Dear Mr. Harrell,</p>
  <div class="letter-body">
    <p>Lorem ipsum dolor sit amet, consectetur adipiscing elit. Donec orci purus, luctus vitae dignissim eu, iaculis sed purus. Vivamus faucibus, ipsum nec aliquet viverra, leo mauris condimentum ligula, sit amet sagittis enim ligula quis arcu. Nam egestas tortor id nisi porttitor mattis. In tortor ante, ultricies in suscipit a, tempus non massa. Vivamus et auctor mi. Fusce vel massa nulla. Phasellus nec eros mauris, et scelerisque orci.</p>
    <p>Donec malesuada orci vitae nulla accumsan porta a id massa. Quisque accumsan iaculis magna sit amet fringilla. Maecenas consequat, magna eget tincidunt semper, odio nibh rutrum mi, id feugiat ante nisi eu risus. Vestibulum nunc orci, rhoncus a placerat in, ultricies in mi. Cras mattis varius eros, vel fringilla nisi suscipit eget. Quisque scelerisque sagittis nulla at porttitor.</p>
    <p>Sed id augue vitae urna euismod commodo aliquet a quam. Pellentesque arcu velit, cursus et malesuada ut, consequat et diam. Nullam erat sem, rhoncus id ullamcorper vitae, rhoncus et arcu. In ultricies ultricies nulla, ut rutrum nisi iaculis at. Donec eu magna a metus ornare faucibus. Fusce aliquet faucibus ultricies. Morbi semper, est id tincidunt gravida, sem arcu adipiscing lacus, ac bibendum nulla leo eu purus. Quisque nec diam sed risus consectetur a ccumsan quis quis nibh. Vestibulum id purus lorem.</p>
    <p>It is a long established fact that a reader will be distracted by the readable content of a page when looking at its layout. The point of using Lorem Ipsum is that it has a more-or-less normal distribution of letters, as opposed to using 'Content here, content here', making it look like readable English. Many desktop publishing packages</p>
  </div>
  <p class="closing">Sincerely,</p>
  <div class="signature" role="img" aria-label="Handwritten signature of Owen Harrell"></div>
  <svg class="letter-corner" viewBox="0 0 410 580" aria-hidden="true">
    <path d="M242 580 Q222 575 228 556 Q230 548 238 541 L327 455 Q343 440 359 455 L410 500 L410 580 Z" fill="var(--navy)"/>
    <path d="M362 450 L410 493" stroke="var(--teal)" stroke-width="2" fill="none"/>
  </svg>
  <div class="letter-contact">
    <div>214 Linden Court</div>
    <div style="margin-bottom:2px">Marlow, Georgia 30418</div>
    <div class="contact-line"><svg class="icon"><use href="#i-phone"/></svg><span>555-310-4821</span></div>
    <div class="contact-line"><svg class="icon"><use href="#i-mobile"/></svg><span>555-782-1093</span></div>
    <div class="contact-line"><svg class="icon"><use href="#i-mail"/></svg><span>hello@vale8.com</span></div>
    <div class="contact-line"><svg class="icon"><use href="#i-web"/></svg><span>www.vale8.com</span></div>
  </div>
</section>
<span class="label" style="left:238px;top:618px">Letterhead</span>

<!-- Envelope -->
<section class="sheet envelope-back" aria-label="Envelope back">
  <div class="body"></div>
  <svg class="flap" viewBox="0 0 354 60" aria-hidden="true">
    <path d="M0 0 H354 L348 30 Q344 59 320 59 H34 Q10 59 6 30 Z" fill="var(--navy)"/>
  </svg>
  <div class="brand"><span class="brand-name">VALE 8</span></div>
</section>
<section class="sheet envelope-front" aria-label="Envelope front">
  <div class="brand">
    <div class="brand-row"><span class="brand-name">VALE 8</span><span class="brand-dot"></span></div>
    <span class="brand-tag">CPAs and Tax Advisors</span>
  </div>
  <div class="return-address">214 Linden Court<br>Marlow, Georgia 30418</div>
</section>
<span class="label" style="left:723px;top:300px">Envelope</span>

<!-- Business card front -->
<section class="sheet card-front" aria-label="Business card front">
  <div class="brand">
    <div class="brand-row"><span class="brand-name">VALE 8</span><span class="brand-dot"></span></div>
    <span class="brand-tag">CPAs and Tax Advisors</span>
  </div>
  <svg class="card-corner" viewBox="0 0 187 107" aria-hidden="true">
    <path d="M88 107 Q74 101 80 88 L142 27 Q154 16 166 27 L187 47 L187 107 Z" fill="var(--navy)"/>
    <path d="M168 24 L187 42" stroke="var(--teal)" stroke-width="1.2" fill="none"/>
  </svg>
  <div class="card-details">
    <div class="card-name">DANA WHITLOCK</div>
    <div class="card-title">President</div>
    <div>214 Linden Court</div>
    <div style="margin-bottom:2px">Marlow, Georgia 30418</div>
    <div class="contact-line"><svg class="icon"><use href="#i-phone"/></svg><span>555-310-4821</span></div>
    <div class="contact-line"><svg class="icon"><use href="#i-mobile"/></svg><span>555-640-2275</span></div>
    <div class="contact-line"><svg class="icon"><use href="#i-mail"/></svg><span>hello@vale8.com</span></div>
    <div class="contact-line"><svg class="icon"><use href="#i-web"/></svg><span>www.vale8.com</span></div>
  </div>
</section>
<span class="label" style="left:1015px;top:153px">Front Card</span>

<!-- Business card back -->
<section class="sheet card-back" role="img" aria-label="Repeating navy pattern of brand marks covering the card back"></section>
<span class="label" style="left:1005px;top:303px">Back Card</span>

<!-- Email signature 1 -->
<section class="sheet email-one" aria-label="Email signature 1">
  <div class="brand">
    <div class="brand-row"><span class="brand-name">VALE 8</span><span class="brand-dot"></span></div>
    <span class="brand-tag">CPAs and Tax Advisors</span>
  </div>
  <div class="person-name">Dana Whitlock</div>
  <div class="person-title">President</div>
  <div class="address">214 Linden Court<br>Marlow, Georgia 30418</div>
  <div class="contacts">
    <div class="contact-line"><svg class="icon"><use href="#i-phone"/></svg><span>555-310-4821</span></div>
    <div class="contact-line"><svg class="icon"><use href="#i-mobile"/></svg><span>555-782-1093</span></div>
    <div class="contact-line"><svg class="icon"><use href="#i-mail"/></svg><span>hello@vale8.com</span></div>
    <div class="contact-line"><svg class="icon"><use href="#i-web"/></svg><span>www.vale8.com</span></div>
  </div>
</section>
<span class="label" style="left:570px;top:611px">Email Signature 1</span>

<!-- Email signature 2 -->
<section class="sheet email-two" aria-label="Email signature 2">
  <div class="brand">
    <div class="brand-row"><span class="brand-name">VALE 8</span><span class="brand-dot"></span></div>
    <span class="brand-tag">CPAs and Tax Advisors</span>
  </div>
  <div class="divider"></div>
  <div class="details">
    <div>214 Linden Court</div>
    <div>Marlow, Georgia 30418</div>
    <div class="contact-line"><svg class="icon"><use href="#i-phone"/></svg><span>555-310-4821</span></div>
    <div class="contact-line"><svg class="icon"><use href="#i-mail"/></svg><span>hello@vale8.com</span></div>
    <div class="contact-line"><svg class="icon"><use href="#i-web"/></svg><span>www.vale8.org</span></div>
  </div>
</section>
<span class="label" style="left:903px;top:484px">Email Signature 2</span>

<!-- Email signature 3 -->
<section class="sheet email-three" aria-label="Email signature 3">
  <div class="brand">
    <div class="brand-row"><span class="brand-name">VALE 8</span><span class="brand-dot"></span></div>
    <span class="brand-tag">CPAs and Tax Advisors</span>
  </div>
  <div class="divider divider-a"></div>
  <div class="address">214 Linden Court<br>Marlow,<br>Georgia 30418</div>
  <div class="divider divider-b"></div>
  <div class="contacts">
    <div class="contact-line"><svg class="icon"><use href="#i-phone"/></svg><span>555-310-4821</span></div>
    <div class="contact-line"><svg class="icon"><use href="#i-mail"/></svg><span>hello@vale8.com</span></div>
    <div class="contact-line"><svg class="icon"><use href="#i-web"/></svg><span>www.vale8.com</span></div>
  </div>
</section>
<span class="label" style="left:916px;top:609px">Email Signature 3</span>

</body>
</html>
```